Thibodeaux Creole

I am launching a new Cajun Steakhouse.
We have purchased a food truck to support the restaurant and sell some our food until the opening in March. 2025. The truck has a white blank canvas on all sides. The right side has multiple raised surfaces (Serving widow,, TV enclosure with speakers, pop up fold-down service table. There is a sliding door on the right with two windows. The bottom window will be covered in wrap. The primary color will be black. Need a bold and fresh design. A Look that will stand out but not be over the top. The truck is a 18’ Ironmule truck (QMB Trick). I have included pictures of the truck, our logo, some pictures of some of the meals that will be served from the truck, a picture of our already branded catering truck, and various other promotional branding we use. The Food truck doesn’t have to look exactly like our catering truck, but I want to keep the black background with our colorful logo. Everything else is can be created.
Our specialty is Garlic Dungenes Crab and that needs to be highlighted (The Best in the Bay).

Target Market(s)

General Public

Industry/Entity Type

Food Service

Font styles to use
Serif
Sans Serif
Decorative
Script

Requirements
Must have
• Black base wrap color
Nice to have
• Look at the mock up on the trash can photo with the little crabs. I think it would look cool on the wrap.
Should not have
• Our specialty is garlic Crabs. So we need to Highlight somewhere (The best crab in the bay)

```html
<!DOCTYPE html>
<html lang="en">
<head>
<meta charset="utf-8">
<title>Thibodeaux Creole Steakhouse – Truck Wrap Side</title>
<link href="https://fonts.googleapis.com/css2?family=Montserrat:wght@700;800&family=Cinzel:wght@400;600&display=swap" rel="stylesheet">
<style>
  :root {
    --page: #ffffff;
    --wrap-black: #000000;
    --ghost: #1c1c1c;
    --orange: #ff8c00;
    --pink: #ec1869;
    --green: #86c124;
    --white: #ffffff;
    --gold: #e9a23a;
    --crab-light: #f59a5c;
    --crab-dark: #e0521f;
    --bun: #d79a52;
    --filling: #c9643a;
  }
  html, body {
    margin: 0;
    padding: 0;
    width: 1200px;
    height: 1043px;
    overflow: hidden;
    background: var(--page);
  }
  .wrap-panel {
    position: absolute;
    left: 0;
    top: 312px;
    width: 1200px;
    height: 420px;
    background: var(--wrap-black);
    overflow: hidden;
    font-family: "Montserrat", Arial, sans-serif;
  }
  .headline-line {
    position: absolute;
    margin: 0;
    font-weight: 800;
    line-height: 1;
    white-space: nowrap;
    text-align: center;
  }
  .headline-best {
    left: 429px; width: 294px; top: 45px;
    font-size: 57px; color: var(--orange);
  }
  .headline-crab {
    left: 380px; width: 390px; top: 92px;
    font-size: 124px; color: var(--pink); letter-spacing: -2px;
  }
  .headline-bay {
    left: 400px; width: 352px; top: 198px;
    font-size: 57px; color: var(--green);
  }
  .contact-phone {
    position: absolute;
    left: 415px; width: 320px; top: 294px;
    margin: 0;
    font-size: 42px; font-weight: 700; line-height: 1;
    color: var(--white); text-align: center;
  }
  .contact-web {
    position: absolute;
    left: 415px; width: 320px; top: 336px;
    margin: 0;
    font-family: "Cinzel", Georgia, serif;
    font-size: 22px; font-weight: 400; line-height: 1;
    color: var(--white); text-align: center;
  }
  .food-image {
    position: absolute;
  }
  .crab-illustration {
    left: 215px; top: 232px; width: 180px; height: 180px;
    border-radius: 50%;
    background: radial-gradient(circle at 50% 45%, var(--crab-light) 0%, var(--crab-dark) 70%, rgba(224,82,31,0) 72%);
  }
  .sandwich-plate {
    left: 754px; top: 218px; width: 148px; height: 100px;
    border-radius: 50%;
    transform: rotate(18deg);
    background: linear-gradient(160deg, #f1f1f1 0%, var(--bun) 45%, #8a9a5a 75%, #e8e8e8 100%);
  }
  .shrimp-poboy {
    left: 968px; top: 290px; width: 220px; height: 72px;
    border-radius: 36px;
    transform: rotate(-30deg);
    background: linear-gradient(180deg, var(--filling) 0%, var(--bun) 60%, #b77a3a 100%);
  }
  .brand-block {
    position: absolute;
    left: 845px; top: 30px; width: 321px;
    text-align: center;
  }
  .brand-mark {
    display: block;
    width: 86px; height: 86px;
    margin: 0 auto 14px;
    border-radius: 50%;
    background: var(--gold);
  }
  .brand-name {
    margin: 0;
    font-family: "Montserrat", Arial, sans-serif;
    font-weight: 700;
    color: var(--gold);
    line-height: 1.15;
  }
  .brand-name-main {
    display: block;
    font-size: 36px;
    letter-spacing: 1px;
  }
  .brand-name-sub {
    display: block;
    font-size: 24px;
  }
</style>
</head>
<body>
  <main class="wrap-panel" aria-label="Thibodeaux Creole Steakhouse food truck wrap, side panel">
    <h1 class="headline-line headline-best">THE BEST</h1>
    <p class="headline-line headline-crab">CRAB</p>
    <p class="headline-line headline-bay">IN THE BAY</p>

    <p class="contact-phone">(555) 014-2298</p>
    <p class="contact-web">Thibcreole.com</p>

    <div class="food-image crab-illustration" role="img" aria-label="Illustration of a whole red Dungeness crab"></div>
    <div class="food-image sandwich-plate" role="img" aria-label="Photo of a fried catfish po'boy on a white plate"></div>
    <div class="food-image shrimp-poboy" role="img" aria-label="Photo of a fried shrimp po'boy with lettuce and tomato"></div>

    <div class="brand-block">
      <span class="brand-mark" aria-hidden="true"></span>
      <p class="brand-name">
        <span class="brand-name-main">THIBODEAUX</span>
        <span class="brand-name-sub">Creole Steakhouse</span>
      </p>
    </div>
  </main>
</body>
</html>
```